Car Dealership Showroom Poster

Design a 3'x5' poster (portiat layout) to advertise our 36 month / 36,000 mile warranty.

Below is a link to our website for color / logo and program details.

https://brockwayautogroupnj.com/

https://brockwayautogroupnj.com/36-month-36000-mile-limited-warranty

https://brockwayautogroupnj.com/36-month-36000-mile-limited-warranty/

```html
<!DOCTYPE html>
<html lang="en">
<head>
<meta charset="utf-8">
<title>Brockway Auto Group – 36 Month / 36,000 Mile Warranty</title>
<link rel="stylesheet" href="https://fonts.googleapis.com/css2?family=Barlow:ital,wght@0,400;0,500;0,600;0,700;0,800;1,600;1,800;1,900&display=swap">
<style>
  :root {
    --green: #126b34;
    --green-dark: #0e5a2b;
    --white: #ffffff;
    --ink: #111111;
    --grey-text: #5a5a5a;
    --arc-grey: #9a9a9a;
    --car-light: #d9d3c6;
    --car-dark: #8f887b;
  }
  * { margin: 0; padding: 0; box-sizing: border-box; }
  html, body { width: 720px; height: 1200px; overflow: hidden; background: var(--white); }
  .poster {
    position: relative; width: 720px; height: 1200px; overflow: hidden;
    font-family: "Barlow", sans-serif; background: var(--white);
  }
  .backdrop { position: absolute; inset: 0; }
  .brand {
    position: absolute; left: 24px; top: 44px; width: 250px;
    color: var(--green); font-weight: 800; font-size: 30px; line-height: 1.05;
    letter-spacing: 0.5px; text-transform: uppercase;
  }
  .offer {
    position: absolute; right: 316px; top: 150px; text-align: right; color: var(--white);
  }
  .offer-price { font-size: 60px; font-weight: 900; font-style: italic; line-height: 1; }
  .offer-line { font-size: 27px; font-weight: 600; font-style: italic; margin-top: 18px; }
  .offer-sub { font-size: 27px; font-weight: 500; margin-top: 8px; }
  .term {
    position: absolute; left: 440px; top: 56px; width: 196px; text-align: center;
    font-style: italic; font-weight: 900; line-height: 1;
  }
  .term-months { font-size: 68px; color: var(--green); }
  .term-label { font-size: 40px; color: var(--ink); margin-top: 20px; }
  .term-miles { font-size: 44px; color: var(--green); margin-top: 20px; }
  .vehicle {
    position: absolute; left: 120px; top: 346px; width: 524px; height: 386px;
    border-radius: 90px 90px 40px 40px;
    background: radial-gradient(ellipse at 50% 40%, var(--car-light), var(--car-dark));
  }
  .intro {
    position: absolute; left: 70px; top: 762px; width: 580px; text-align: center;
    color: var(--grey-text); font-size: 19px; line-height: 1.65;
  }
  .features { position: absolute; left: 0; top: 902px; width: 720px; }
  .feature { position: absolute; width: 200px; text-align: center; }
  .feature-icon {
    width: 76px; height: 76px; border-radius: 50%; background: var(--green);
    margin: 0 auto 20px; display: flex; align-items: center; justify-content: center;
  }
  .feature-label { color: var(--grey-text); font-size: 19px; font-weight: 600; line-height: 1.3; }
  .contact {
    position: absolute; left: 0; top: 1110px; width: 720px; color: var(--white); text-align: center;
  }
  .contact-row { display: flex; align-items: center; justify-content: center; gap: 12px; }
  .contact-phone { font-size: 24px; font-weight: 800; font-style: italic; }
  .contact-address { font-size: 23px; font-weight: 700; margin-top: 12px; }
</style>
</head>
<body>
<div class="poster">
  <svg class="backdrop" width="720" height="1200" viewBox="0 0 720 1200" aria-hidden="true">
    <path d="M0 0 H720 V436 Q360 250 0 402 Z" fill="var(--green)"/>
    <path d="M0 410 Q360 258 720 444" fill="none" stroke="var(--arc-grey)" stroke-width="5"/>
    <circle cx="150" cy="0" r="164" fill="var(--white)"/>
    <rect x="440" y="0" width="196" height="420" fill="var(--white)"/>
    <rect x="642" y="0" width="6" height="420" fill="var(--white)"/>
    <path d="M0 1200 V1160 Q360 1000 720 1160 V1200 Z" fill="var(--green)"/>
  </svg>

  <div class="brand">Brockway<br>Auto Group</div>

  <div class="offer">
    <div class="offer-price">$50</div>
    <div class="offer-line">Deductible &amp;</div>
    <div class="offer-sub">Nationwide Coverage!</div>
  </div>

  <div class="term">
    <div class="term-months">36</div>
    <div class="term-label">MONTH</div>
    <div class="term-miles">36,000</div>
    <div class="term-label">MILE</div>
  </div>

  <div class="vehicle" role="img" aria-label="Photo of a champagne-coloured sedan, front view"></div>

  <p class="intro">At Brockway Auto Group, your peace of mind comes standard. Every vehicle we sell undergoes a thorough multi-point inspection and full reconditioning before it ever reaches the lot.</p>

  <div class="features">
    <div class="feature" style="left:40px">
      <div class="feature-icon">
        <svg width="38" height="38" viewBox="0 0 24 24" fill="none" stroke="#fff" stroke-width="2"><path d="M12 22s7-7 7-12a7 7 0 0 0-14 0c0 5 7 12 7 12z"/><circle cx="12" cy="10" r="2.5"/></svg>
      </div>
      <div class="feature-label">Nationwide<br>coverage</div>
    </div>
    <div class="feature" style="left:256px">
      <div class="feature-icon">
        <svg width="38" height="38" viewBox="0 0 24 24" fill="none" stroke="#fff" stroke-width="2"><path d="M3 12 12 3h8v8l-9 9z"/><circle cx="16" cy="8" r="1.6"/></svg>
      </div>
      <div class="feature-label">Only a $50<br>deductible</div>
    </div>
    <div class="feature" style="left:472px">
      <div class="feature-icon">
        <svg width="38" height="38" viewBox="0 0 24 24" fill="none" stroke="#fff" stroke-width="2"><circle cx="12" cy="12" r="8"/><path d="M8.5 12.2l2.4 2.4 4.6-4.8"/></svg>
      </div>
      <div class="feature-label">Comprehensive<br>you can rely on</div>
    </div>
  </div>

  <div class="contact">
    <div class="contact-row contact-phone">
      <svg width="26" height="26" viewBox="0 0 24 24"><circle cx="12" cy="12" r="12" fill="#fff"/><path d="M8 6l2 3-1.2 1.4a7 7 0 0 0 4.8 4.8L15 14l3 2-1 2.2c-5 .4-11-5.6-10.6-10.6z" fill="var(--green)"/></svg>
      <span>(609) 555-0182</span>
    </div>
    <div class="contact-row contact-address">
      <svg width="26" height="26" viewBox="0 0 24 24"><path d="M12 23s8-8 8-13a8 8 0 0 0-16 0c0 5 8 13 8 13z" fill="#fff"/><circle cx="12" cy="10" r="3" fill="var(--green)"/></svg>
      <span>214 Harbor Rd, Millbrook, NJ 08299</span>
    </div>
  </div>
</div>
</body>
</html>
```